I'm looking for a smart new design for business cards

Industry/Entity Type

Commercial Electrical

Contact Information for Business Card

Logo, name, email, position, website QR

Requirements
Nice to have
• Logo embedded behind the text side

```html
<!DOCTYPE html>
<html lang="en">
<head>
<meta charset="utf-8">
<title>Northline Electrical – Business Card</title>
<link href="https://fonts.googleapis.com/css2?family=Montserrat:wght@400;500;700&display=swap" rel="stylesheet">
<style>
  :root {
    --bg: #1c1c1c;
    --card: #ffffff;
    --navy: #2b2e7c;
    --red: #e2232f;
    --ink: #333333;
  }
  html, body {
    margin: 0;
    padding: 0;
    width: 1200px;
    height: 1059px;
    overflow: hidden;
    background: var(--bg);
    font-family: "Montserrat", sans-serif;
  }
  .card {
    position: absolute;
    left: 190px;
    top: 296px;
    width: 820px;
    height: 468px;
    background: var(--card);
    border-radius: 24px;
  }
  .brand {
    position: absolute;
    left: 40px;
    top: 180px;
    width: 370px;
    display: flex;
    align-items: center;
    justify-content: center;
    gap: 14px;
  }
  .brand-dot {
    width: 30px;
    height: 30px;
    border-radius: 50%;
    background: var(--red);
    flex: none;
  }
  .brand-name {
    font-weight: 700;
    font-size: 34px;
    line-height: 1.1;
    color: var(--navy);
    letter-spacing: 0.5px;
  }
  .divider {
    position: absolute;
    left: 424px;
    top: 108px;
    width: 2px;
    height: 252px;
    background: var(--red);
  }
  .details {
    position: absolute;
    left: 458px;
    top: 100px;
    color: var(--ink);
  }
  .person-name {
    margin: 0;
    font-weight: 700;
    font-size: 38px;
    line-height: 1.1;
    color: var(--navy);
  }
  .person-name .surname { color: var(--red); }
  .role {
    margin: 6px 0 0;
    font-size: 21px;
    font-weight: 500;
  }
  .address {
    margin: 22px 0 0;
    font-size: 21px;
    line-height: 33px;
    font-style: normal;
  }
  .contacts {
    list-style: none;
    margin: 14px 0 0;
    padding: 0;
    font-size: 21px;
  }
  .contacts li {
    display: flex;
    align-items: center;
    gap: 9px;
    height: 32.5px;
  }
  .contacts svg { width: 18px; height: 18px; flex: none; }
</style>
</head>
<body>
  <div class="card">
    <div class="brand">
      <span class="brand-dot"></span>
      <span class="brand-name">Northline<br>Electrical</span>
    </div>

    <div class="divider"></div>

    <div class="details">
      <h1 class="person-name">Daniel <span class="surname">Harper</span></h1>
      <p class="role">Managing Director</p>
      <address class="address">Your address, City<br>State, Zip 1234</address>
      <ul class="contacts">
        <li>
          <svg viewBox="0 0 20 20" aria-hidden="true"><path fill="#e2232f" d="M2 8c0-3 4-5 8-5s8 2 8 5l-3 1-1-2H6L5 9zM5 10h10l2 7H3z"/></svg>
          <span>123 456 789</span>
        </li>
        <li>
          <svg viewBox="0 0 20 20" aria-hidden="true"><rect x="1" y="4" width="18" height="12" fill="#e2232f"/><path d="M1 4l9 7 9-7M1 16l7-6M19 16l-7-6" stroke="#fff" stroke-width="1.5" fill="none"/></svg>
          <span>info@yourgmail.com</span>
        </li>
        <li>
          <svg viewBox="0 0 20 20" aria-hidden="true"><circle cx="10" cy="10" r="9" fill="#e2232f"/><path d="M4 6c2 0 3 2 5 2s1 3-1 4 0 4-2 5M13 3c0 2 2 3 4 3M12 12c2 0 3 1 3 4" stroke="#fff" stroke-width="1.6" fill="none"/></svg>
          <span>www.yourwebsite.com</span>
        </li>
      </ul>
    </div>
  </div>
</body>
</html>
```